packing for cake and sweet

we need packing design for cake box.
I attached some nice packing from other shop like :
Vira and belmonde for examples.

I attached the logo.
you can make packing with any colors you choose.

box size :
length : 30 cm
Width : 30 cm
Height : 15 cm

this shops have very good design :
https://www.brambleworth.example/hot-chocolate/discover-hot-chocolate/all-hot-chocolate

Industry/Entity Type

food

Font styles to use
Other font styles liked:
• same our logo already attached.

```html
<!DOCTYPE html>
<html lang="en">
<head>
<meta charset="utf-8">
<title>Marivelle – Cake Box Colour Options</title>
<link rel="stylesheet" href="https://fonts.googleapis.com/css2?family=Cinzel:wght@400&family=Raleway:wght@400&display=swap">
<style>
  :root {
    --page: #ffffff;
    --sky: #e2f3fc;
    --card: #fcf8f9;
    --rose: #e2768c;
    --salmon: #f5aea5;
    --sand: #ecdcc7;
    --apricot: #f9ae6d;
    --petal-pink: #f4b9c8;
    --petal-peach: #fbd9cc;
    --leaf: #c4d6e8;
    --caption: #8a8a8f;
  }
  * { box-sizing: border-box; margin: 0; padding: 0; }
  html, body {
    width: 1200px; height: 1200px; overflow: hidden;
    background: var(--page);
  }
  .sheet { position: relative; width: 1200px; height: 1200px; }

  .box-panel {
    position: absolute; left: 175px; width: 688px; height: 487px;
    background: var(--sky); overflow: hidden;
  }
  .box-panel--rose { top: 90px; }
  .box-panel--apricot { top: 624px; }

  .floral {
    position: absolute;
    border-radius: 45%;
  }
  .floral--top {
    left: 213px; top: -20px; width: 401px; height: 191px;
    background:
      radial-gradient(ellipse 30% 45% at 78% 55%, var(--petal-peach) 60%, transparent 72%),
      radial-gradient(ellipse 22% 45% at 45% 45%, #fde6dc 60%, transparent 72%),
      radial-gradient(ellipse 18% 40% at 18% 55%, var(--petal-pink) 60%, transparent 72%),
      radial-gradient(ellipse 50% 50% at 55% 40%, var(--leaf) 40%, transparent 70%);
  }
  .floral--left {
    left: 45px; top: 183px; width: 122px; height: 274px;
    background:
      radial-gradient(ellipse 55% 28% at 65% 52%, var(--petal-pink) 60%, transparent 75%),
      radial-gradient(ellipse 55% 25% at 50% 82%, var(--leaf) 55%, transparent 75%),
      radial-gradient(ellipse 30% 25% at 70% 18%, var(--leaf) 55%, transparent 75%);
  }
  .floral--right {
    left: 500px; top: 208px; width: 90px; height: 180px;
    background:
      radial-gradient(ellipse 50% 38% at 40% 40%, var(--petal-peach) 60%, transparent 75%),
      radial-gradient(ellipse 25% 25% at 25% 85%, var(--leaf) 55%, transparent 75%);
  }
  .floral--bottom {
    left: 223px; top: 430px; width: 245px; height: 80px;
    background:
      radial-gradient(ellipse 30% 50% at 25% 60%, var(--petal-peach) 60%, transparent 75%),
      radial-gradient(ellipse 25% 50% at 72% 55%, #fde6dc 60%, transparent 75%);
  }

  .label-card {
    position: absolute; left: 160px; top: 89px;
    width: 350px; height: 350px;
    background: var(--card);
    text-align: center;
  }
  .brand-name {
    margin-top: 134px;
    font-family: "Cinzel", serif;
    font-weight: 400;
    font-size: 50px;
    line-height: 1;
    letter-spacing: 0.5px;
  }
  .label-card--rose .brand-name { color: var(--rose); }
  .label-card--apricot .brand-name { color: var(--apricot); }
  .tagline {
    margin-top: 12px;
    font-family: "Raleway", sans-serif;
    font-size: 11.5px;
    letter-spacing: 2px;
    color: var(--caption);
  }

  .swatch-row {
    position: absolute; left: 908px; display: flex; gap: 11px;
  }
  .swatch-row--rose { top: 160px; }
  .swatch-row--apricot { top: 759px; }
  .swatch { width: 52px; height: 257px; }
  .swatch--rose { background: var(--rose); }
  .swatch--salmon { background: var(--salmon); }
  .swatch--sand { background: var(--sand); }
  .swatch--apricot { background: var(--apricot); }
</style>
</head>
<body>
<main class="sheet">

  <section class="box-panel box-panel--rose">
    <div class="floral floral--top" role="img" aria-label="Bouquet of pink carnations, peach roses and dusty miller leaves"></div>
    <div class="floral floral--left" role="img" aria-label="Pink carnation with dusty miller leaves"></div>
    <div class="floral floral--right" role="img" aria-label="Peach carnation with silver leaf"></div>
    <div class="floral floral--bottom" role="img" aria-label="Peach roses and carnations along the lower edge"></div>
    <div class="label-card label-card--rose">
      <h1 class="brand-name">Marivelle</h1>
      <p class="tagline">Lorem ipsum Lorem ipsum</p>
    </div>
  </section>

  <div class="swatch-row swatch-row--rose">
    <div class="swatch swatch--rose"></div>
    <div class="swatch swatch--salmon"></div>
    <div class="swatch swatch--sand"></div>
  </div>

  <section class="box-panel box-panel--apricot">
    <div class="floral floral--top" role="img" aria-label="Bouquet of pink carnations, peach roses and dusty miller leaves"></div>
    <div class="floral floral--left" role="img" aria-label="Pink carnation with dusty miller leaves"></div>
    <div class="floral floral--right" role="img" aria-label="Peach carnation with silver leaf"></div>
    <div class="floral floral--bottom" role="img" aria-label="Peach roses and carnations along the lower edge"></div>
    <div class="label-card label-card--apricot">
      <h2 class="brand-name">Marivelle</h2>
      <p class="tagline">Lorem ipsum Lorem ipsum</p>
    </div>
  </section>

  <div class="swatch-row swatch-row--apricot">
    <div class="swatch swatch--apricot"></div>
    <div class="swatch swatch--salmon"></div>
    <div class="swatch swatch--sand"></div>
  </div>

</main>
</body>
</html>
```